Varnex Consulting Business card design.

See our website www.varnexconsulting.example which will give you a good idea of what we are about. The font is called 'Play'.

I'd like a standout business card in keeping with the themes and branding on the website

Target Market(s)

professionals. HR directors

Industry/Entity Type

Business

Contact Information for Business Card

Varnex Consulting PO Box 3172 Merrowdale NSW 2291 1300 485 193 Gavin Threlkeld Principal email: career@varnexconsulting.example ABN: 71203948865

Font styles to use
Other font styles liked:
• Play

Requirements
Must have
• Must have same design colours and branding as website.
• On back I'd prefer a list of the things we do which appears below the name at the header on the website

```html
<!DOCTYPE html>
<html lang="en">
<head>
<meta charset="utf-8">
<title>Varnex Consulting – Business Card</title>
<link rel="stylesheet" href="https://fonts.googleapis.com/css2?family=Play:wght@400;700&display=swap">
<style>
  :root {
    --stage: #e9e6e1;
    --navy: #0b2a40;
    --navy-deep: #071d2e;
    --sky: #2ea3e6;
    --paper: #ffffff;
    --ink: #1d2f3d;
    --grey: #5d656c;
    --rule: #c9cdd1;
  }
  * { margin: 0; padding: 0; box-sizing: border-box; }
  html, body { width: 1200px; height: 950px; overflow: hidden; }
  body {
    background: var(--stage);
    font-family: 'Play', sans-serif;
    display: flex;
    flex-direction: column;
    align-items: center;
    justify-content: center;
    gap: 40px;
  }
  .card {
    width: 740px;
    height: 423px;
    position: relative;
    overflow: hidden;
    box-shadow: 0 10px 28px rgba(0,0,0,0.18);
  }

  /* Front */
  .card-front {
    background: linear-gradient(135deg, var(--navy) 0%, var(--navy-deep) 100%);
    color: var(--paper);
  }
  .card-front .wordmark {
    position: absolute;
    left: 50%;
    top: 170px;
    transform: translateX(-50%);
    font-size: 38px;
    letter-spacing: 3px;
    white-space: nowrap;
    text-transform: uppercase;
    color: var(--paper);
  }
  .services {
    position: absolute;
    left: 0; right: 0;
    bottom: 58px;
    text-align: center;
    font-size: 17px;
    letter-spacing: 0.5px;
    white-space: nowrap;
    color: var(--paper);
  }
  .services .sep { color: var(--sky); margin: 0 8px; }

  /* Back */
  .card-back {
    background: var(--paper);
    color: var(--ink);
  }
  .card-back .wordmark {
    position: absolute;
    left: 44px;
    top: 196px;
    width: 296px;
    font-size: 23px;
    letter-spacing: 2px;
    white-space: nowrap;
    text-transform: uppercase;
    color: var(--navy);
  }
  .divider {
    position: absolute;
    left: 370px;
    top: 95px;
    width: 1px;
    height: 240px;
    background: linear-gradient(to bottom, transparent, var(--rule) 20%, var(--rule) 80%, transparent);
  }
  .contact {
    position: absolute;
    left: 396px;
    top: 100px;
    width: 330px;
  }
  .contact .person-name {
    font-size: 26px;
    font-weight: 700;
    color: var(--ink);
    line-height: 1.1;
    white-space: nowrap;
  }
  .contact .person-role {
    font-size: 18px;
    color: var(--sky);
    margin-bottom: 14px;
  }
  .contact .address {
    font-size: 17px;
    color: var(--grey);
    line-height: 1.3;
    margin-bottom: 4px;
  }
  .contact-line {
    display: flex;
    align-items: center;
    gap: 9px;
    font-size: 17px;
    color: var(--grey);
    line-height: 1.55;
    white-space: nowrap;
  }
  .contact-line svg { width: 15px; height: 15px; flex: none; fill: var(--ink); }
</style>
</head>
<body>

  <section class="card card-front" aria-label="Business card front">
    <div class="wordmark">Varnex Consulting</div>
    <p class="services">
      Search &amp; Select<span class="sep">|</span>Career<span class="sep">|</span>Coaching<span class="sep">|</span>Leadership<span class="sep">|</span>Outplacement
    </p>
  </section>

  <section class="card card-back" aria-label="Business card back">
    <div class="wordmark">Varnex Consulting</div>
    <div class="divider"></div>
    <div class="contact">
      <h1 class="person-name">Gavin Threlkeld</h1>
      <p class="person-role">Principal</p>
      <p class="address">PO Box 3172 Merrowdale<br>NSW 2291</p>
      <p class="contact-line">
        <svg viewBox="0 0 16 16" aria-hidden="true"><path d="M2 3c0-.6.4-1 1-1h2.2l1.2 3-1.5 1.1a8 8 0 0 0 4 4L10 8.6l3 1.2V12c0 .6-.4 1-1 1C6.5 13 2 8.5 2 3z"/></svg>
        1300 485 193
      </p>
      <p class="contact-line">
        <svg viewBox="0 0 16 16" aria-hidden="true"><path d="M1 4h14v9H1z M1.8 4.6 8 9.2l6.2-4.6" stroke="#fff" stroke-width="1"/></svg>
        career@varnexconsulting.example
      </p>
      <p class="contact-line">
        <svg viewBox="0 0 16 16" aria-hidden="true"><circle cx="8" cy="8" r="7"/><path d="M1 8h14M8 1c2.5 2.5 2.5 11.5 0 14M8 1c-2.5 2.5-2.5 11.5 0 14" stroke="#fff" stroke-width="1" fill="none"/></svg>
        www.varnexconsulting.example
      </p>
    </div>
  </section>

</body>
</html>
```